Varelko App for Smart Devices IoT WiFi Electronic

Varelko is a siren manufacturer. This application is used for the company's products that have a Wi-Fi connection and an internet connection, which can be configured and activated remotely through this application. In addition, this application is used to activate the siren at specific times for the start and end of shifts in companies and schools. Users will be siren installers and IT or HR managers.
In addition to activating motorized sirens timers, some siren models have speakers and allow you to play TTS (text to speech) audio, audio recorded by the user on the phone and upload audio (mp3) with playlist programming with start and end times.
Application screens: home with dashboard (one dashboard for each category). Device categories: timers, speakers, motorized siren. Screen for requesting evaluation in the Play Store. Screen for registering the user profile. Screen for registering devices according to their category (timers, speakers, motorized siren). Screen for registering device groups. Screen for pairing the device on the client's Wi-Fi network. Screen for registering activation times. Screen for uploading MP3 audios. Screen for registering playlists with audio selection, start and end times. Screen for recording audio for later sending to the speakers. Screen for converting text to speech and sending to the speakers. It is important to have a time picker with the day of the week to program the activation times and playlist.

Target Market(s)

Schools, Companies and Stores.

Industry/Entity Type

IoT

Font styles to use
Sans Serif
Other font styles liked:
• roboto

Colors
FFC000
F8CF3A
FAE287
FDF2CF
FEFAEE

Requirements
Must have
• time picker with weekdays for timer programming feature.
Nice to have
• app review request screen on play store

```html
<!DOCTYPE html>
<html lang="en">
<head>
<meta charset="utf-8">
<title>Speakers – Device Setup</title>
<link rel="stylesheet" href="https://fonts.googleapis.com/css2?family=Poppins:wght@500;600;700&display=swap">
<style>
  :root{
    --brand:#f8be00;
    --brand-soft:#fdf2cf;
    --ink:#4a5160;
    --ink-soft:#5b6270;
    --muted:#a9afbd;
    --line:#e3e5ea;
    --screen:#f5f6fa;
    --card:#ffffff;
    --pill:#f0f1f4;
    --online:#4cc85a;
    --page:#ffffff;
  }
  *{box-sizing:border-box;margin:0;padding:0}
  html,body{width:677px;height:1200px;overflow:hidden;background:var(--page);
    font-family:"Poppins",sans-serif;color:var(--ink)}
  .canvas{position:relative;width:677px;height:1200px}
  .screen{position:absolute;left:111px;top:85px;width:484px;height:1045px;
    border-radius:48px;background:var(--screen);overflow:hidden}
  .header-shape{position:absolute;left:0;top:0}
  .abs{position:absolute}
  .status-time{left:39px;top:18px;font-size:17px;font-weight:600;color:var(--ink)}
  .status-icons{left:384px;top:20px}
  .back{left:22px;top:88px}
  .title{left:0;width:484px;top:76px;text-align:center;color:#fff;font-size:32px;font-weight:700}
  .avatar{left:397px;top:66px;width:60px;height:60px;border-radius:50%;border:3px solid #fff;
    background:radial-gradient(circle at 50% 40%,#d9b8a0,#8a6a55 70%,#cfd3da)}
  .online{left:443px;top:69px;width:14px;height:14px;border-radius:50%;background:var(--online);border:2px solid #fff}
  .card{position:absolute;left:24px;width:433px;background:var(--card);border-radius:16px;
    box-shadow:0 10px 28px rgba(60,70,100,.08)}
  .card-title{position:absolute;left:37px;font-size:21px;font-weight:600;color:var(--ink)}
  .field{position:absolute;height:58px;border:1.5px solid var(--line);border-radius:29px;
    display:flex;align-items:center;justify-content:space-between;padding:0 18px;
    font-size:13.5px;font-weight:500;color:var(--ink-soft)}
  .radios{position:absolute;display:flex;gap:18px;font-size:12.5px;font-weight:500;color:var(--ink-soft)}
  .radio{display:flex;align-items:center;gap:4px}
  .radio::before{content:"";width:11px;height:11px;border-radius:50%;border:2px solid var(--ink-soft)}
  .radio.is-active{color:var(--brand)}
  .radio.is-active::before{border-color:var(--brand);background:radial-gradient(circle,var(--brand) 40%,transparent 45%)}
  .wave{left:35px;top:111px;width:287px;height:62px;border-radius:31px;background:var(--pill)}
  .mic{left:332px;top:111px;width:62px;height:62px;border-radius:50%;background:var(--brand);
    display:flex;align-items:center;justify-content:center}
  .divider{position:absolute;left:35px;top:115px;width:363px;height:1px;background:var(--line)}
  .nav{left:0;top:943px;width:484px;height:102px;background:#fff}
  .nav-icon{position:absolute;top:22px}
  .home-bar{left:150px;top:78px;width:175px;height:6px;border-radius:3px;background:var(--muted)}
</style>
</head>
<body>
<div class="canvas">
  <div class="screen">
    <svg class="header-shape" width="484" height="200" viewBox="0 0 484 200">
      <path d="M0 0 H484 V150 Q484 165 470 188 L460 200 H24 L14 188 Q0 165 0 150 Z" fill="var(--brand)"/>
    </svg>

    <div class="abs status-time">9:41</div>
    <svg class="abs status-icons" width="76" height="14" viewBox="0 0 76 14">
      <g fill="var(--ink)">
        <rect x="0" y="9" width="3" height="4" rx="1"/><rect x="5" y="6" width="3" height="7" rx="1"/>
        <rect x="10" y="3" width="3" height="10" rx="1"/><rect x="15" y="0" width="3" height="13" rx="1"/>
      </g>
      <path d="M24 5 Q32 -1 40 5 M27 8 Q32 4 37 8" stroke="var(--ink)" stroke-width="2" fill="none" stroke-linecap="round"/>
      <circle cx="32" cy="11" r="1.8" fill="var(--ink)"/>
      <rect x="49" y="1" width="22" height="12" rx="3" fill="none" stroke="var(--ink)" stroke-width="1.5"/>
      <rect x="51" y="3" width="18" height="8" rx="1.5" fill="var(--ink)"/>
      <rect x="72.5" y="5" width="2" height="4" rx="1" fill="var(--ink)"/>
    </svg>

    <svg class="abs back" width="16" height="22" viewBox="0 0 16 22">
      <path d="M12 3 L4 11 L12 19" stroke="#fff" stroke-width="3" fill="none" stroke-linecap="round" stroke-linejoin="round"/>
    </svg>
    <div class="abs title">Speakers</div>
    <div class="abs avatar" role="img" aria-label="User profile photo"></div>
    <div class="abs online"></div>

    <section class="card" style="top:177px;height:375px">
      <div class="card-title" style="top:28px">Select Device</div>
      <div class="field" style="left:35px;top:73px;width:359px">Select
        <svg width="14" height="9" viewBox="0 0 14 9"><path d="M2 2 L7 7 L12 2" stroke="var(--muted)" stroke-width="2" fill="none" stroke-linecap="round"/></svg>
      </div>
      <div class="card-title" style="top:158px">Activation Timer</div>
      <div class="field" style="left:35px;top:204px;width:174px">Start Date
        <svg width="20" height="20" viewBox="0 0 20 20"><rect x="2" y="3" width="16" height="15" rx="2" fill="none" stroke="var(--muted)" stroke-width="1.4"/><path d="M2 7 H18 M6 1 V4 M14 1 V4" stroke="var(--muted)" stroke-width="1.4"/><g fill="var(--muted)"><rect x="5" y="9" width="2" height="2"/><rect x="9" y="9" width="2" height="2"/><rect x="13" y="9" width="2" height="2"/><rect x="5" y="13" width="2" height="2"/><rect x="9" y="13" width="2" height="2"/><rect x="13" y="13" width="2" height="2"/></g></svg>
      </div>
      <div class="field" style="left:220px;top:204px;width:174px">End Date
        <svg width="20" height="20" viewBox="0 0 20 20"><rect x="2" y="3" width="16" height="15" rx="2" fill="none" stroke="var(--muted)" stroke-width="1.4"/><path d="M2 7 H18 M6 1 V4 M14 1 V4" stroke="var(--muted)" stroke-width="1.4"/><g fill="var(--muted)"><rect x="5" y="9" width="2" height="2"/><rect x="9" y="9" width="2" height="2"/><rect x="13" y="9" width="2" height="2"/><rect x="5" y="13" width="2" height="2"/><rect x="9" y="13" width="2" height="2"/><rect x="13" y="13" width="2" height="2"/></g></svg>
      </div>
      <div class="field" style="left:35px;top:282px;width:359px">Select Time
        <svg width="20" height="20" viewBox="0 0 20 20"><circle cx="10" cy="10" r="8" fill="none" stroke="var(--muted)" stroke-width="1.5"/><path d="M10 5 V10 L13 12" stroke="var(--muted)" stroke-width="1.5" fill="none" stroke-linecap="round"/></svg>
      </div>
    </section>

    <section class="card" style="top:581px;height:207px">
      <div class="card-title" style="top:22px">Audio Configuration</div>
      <div class="radios" style="left:35px;top:68px">
        <span class="radio is-active">Record Voice</span>
        <span class="radio">Text to Speech</span>
      </div>
      <div class="abs wave">
        <svg width="287" height="62" viewBox="0 0 287 62">
          <g stroke-linecap="round" stroke-width="2.5">
            <g stroke="var(--ink-soft)">
              <path d="M28 26V36M34 22V40M40 18V44M46 24V38M52 14V48M58 20V42M64 24V38M70 16V46M76 22V40M82 26V36M88 20V42M94 14V48M100 24V38M106 22V40M112 18V44"/>
            </g>
            <g stroke="#c3c7d0">
              <path d="M118 20V42M124 24V38M130 16V46M136 22V40M142 26V36M148 18V44M154 24V38M160 14V48M166 22V40M172 26V36M178 18V44M184 22V40M190 24V38M196 16V46M202 20V42M208 26V36M214 22V40M220 18V44M226 24V38M232 14V48M238 22V40M244 26V36M250 28V34"/>
            </g>
          </g>
        </svg>
      </div>
      <div class="abs mic">
        <svg width="24" height="32" viewBox="0 0 24 32"><rect x="7" y="1" width="10" height="18" rx="5" fill="#fff"/><path d="M3 14 Q3 24 12 24 Q21 24 21 14 M12 24 V30 M7 30 H17" stroke="#fff" stroke-width="2" fill="none" stroke-linecap="round"/></svg>
      </div>
    </section>

    <section class="card" style="top:815px;height:220px">
      <div class="card-title" style="top:22px">Repeat Activation</div>
      <div class="radios" style="left:38px;top:69px;gap:16px">
        <span class="radio">Only Once</span>
        <span class="radio">Daily</span>
        <span class="radio">Weekly</span>
        <span class="radio is-active" style="margin-left:6px">Custom Input</span>
      </div>
      <div class="divider"></div>
    </section>

    <nav class="abs nav">
      <svg class="nav-icon" style="left:61px" width="28" height="28" viewBox="0 0 28 28"><path d="M3 12 L14 3 L25 12 V24 Q25 26 23 26 H18 V18 H10 V26 H5 Q3 26 3 24 Z" fill="var(--brand)"/></svg>
      <svg class="nav-icon" style="left:170px" width="32" height="32" viewBox="0 0 32 32"><circle cx="16" cy="16" r="16" fill="var(--muted)"/><path d="M16 9 V23 M9 16 H23" stroke="#fff" stroke-width="3" stroke-linecap="round"/></svg>
      <svg class="nav-icon" style="left:282px" width="28" height="32" viewBox="0 0 28 32"><path d="M14 2 Q22 2 22 12 V20 L26 25 H2 L6 20 V12 Q6 2 14 2 Z" fill="var(--muted)"/><circle cx="14" cy="28" r="3.5" fill="var(--muted)"/></svg>
      <svg class="nav-icon" style="left:390px" width="32" height="32" viewBox="0 0 32 32"><g fill="var(--muted)"><circle cx="16" cy="16" r="11"/><g transform="translate(16 16)"><rect x="-3.5" y="-16" width="7" height="8" rx="1.5"/><rect x="-3.5" y="-16" width="7" height="8" rx="1.5" transform="rotate(45)"/><rect x="-3.5" y="-16" width="7" height="8" rx="1.5" transform="rotate(90)"/><rect x="-3.5" y="-16" width="7" height="8" rx="1.5" transform="rotate(135)"/><rect x="-3.5" y="-16" width="7" height="8" rx="1.5" transform="rotate(180)"/><rect x="-3.5" y="-16" width="7" height="8" rx="1.5" transform="rotate(225)"/><rect x="-3.5" y="-16" width="7" height="8" rx="1.5" transform="rotate(270)"/><rect x="-3.5" y="-16" width="7" height="8" rx="1.5" transform="rotate(315)"/></g></g><circle cx="16" cy="16" r="5" fill="#fff"/></svg>
      <div class="abs home-bar"></div>
    </nav>
  </div>
</div>
</body>
</html>
```